REAL PSYCHIC rear window decal. Mystical, light, positive, spiritual coach vibes

Design a sign for my back car window.
HOT PINK and purple swirly, mystical sign. Eye-catching and classy.
Size 24” x 18”
TEXT:
MARLOWE DESTRY
Psychic & Medium
Www,.marlowedestry.com
World Renowned for Over 45 Years. (This last line make small at bottom)

*This is not a filled in magnet, it will be transparent.

Target Market(s)

Women

Industry/Entity Type

Spirituality

Font styles to use
Script
Other font styles liked:
• See upload for a font I like

Colors
E54698
E96AAD
F1A4CE
F9D9EA
FCEFF6
A7469A
B969AE
D3A5CF
EDDBEB
F8F0F9
6B429C
8869AF
B7A5CE
E3DAEB
F3F0F8

Requirements
Must have
• Pink purple, classy yet mystical vibe
Nice to have
• Easy to read, but old-timey classic font for “MARLOWE DESTRY”

```html
<!DOCTYPE html>
<html lang="en">
<head>
<meta charset="utf-8">
<title>Marlowe Destry – Psychic &amp; Medium Window Decal</title>
<link rel="stylesheet" href="https://fonts.googleapis.com/css2?family=Great+Vibes&family=Pinyon+Script&family=Lobster&family=Playfair+Display:wght@700&display=swap">
<style>
  :root {
    --hot-pink: #E54698;
    --deep-purple: #6B429C;
    --soft-purple: #8869AF;
    --blush: #F9D9EA;
    --lavender: #B7A5CE;
    --frame: #B4B4B4;
    --paper: #FFFFFF;
  }
  html, body {
    margin: 0;
    padding: 0;
    width: 1200px;
    height: 1200px;
    overflow: hidden;
    background: var(--paper);
  }
  .canvas {
    position: relative;
    width: 1200px;
    height: 1200px;
    background: var(--paper);
  }
  .decal {
    position: absolute;
    left: 78px;
    top: 209px;
    width: 1044px;
    height: 782px;
    box-sizing: border-box;
    border: 1.5px solid var(--frame);
  }
  .decal-art {
    position: absolute;
    inset: 0;
    width: 1200px;
    height: 1200px;
  }
  .client-name {
    font-family: "Great Vibes", cursive;
    fill: var(--hot-pink);
  }
  .service-line {
    font-family: "Lobster", cursive;
    fill: var(--deep-purple);
  }
  .web-address {
    font-family: "Playfair Display", serif;
    font-weight: 700;
    fill: var(--soft-purple);
    letter-spacing: 1px;
  }
  .tagline {
    font-family: "Pinyon Script", cursive;
    fill: var(--soft-purple);
  }
</style>
</head>
<body>
<main class="canvas">
  <div class="decal"></div>
  <svg class="decal-art" viewBox="0 0 1200 1200" xmlns="http://www.w3.org/2000/svg">
    <defs>
      <linearGradient id="gaze-tones" x1="0" y1="0" x2="0" y2="1">
        <stop offset="0" stop-color="var(--blush)"/>
        <stop offset="1" stop-color="var(--lavender)"/>
      </linearGradient>
      <path id="service-arc" d="M 315 815 Q 600 690 885 815"/>
      <path id="web-arc" d="M 405 848 Q 600 800 795 848"/>
    </defs>

    <text class="client-name" x="600" y="462" text-anchor="middle" font-size="150"
          textLength="980" lengthAdjust="spacingAndGlyphs">Marlowe Destry</text>

    <rect class="gaze-illustration" x="348" y="516" width="504" height="132" rx="60"
          fill="url(#gaze-tones)" role="img"
          aria-label="Illustration of a pair of mystical eyes with pink lids and purple lashes"/>

    <text class="service-line" font-size="72">
      <textPath href="#service-arc" startOffset="50%" text-anchor="middle">Psychic &amp; Medium</textPath>
    </text>

    <text class="web-address" font-size="29">
      <textPath href="#web-arc" startOffset="50%" text-anchor="middle">www.marlowedestry.com</textPath>
    </text>

    <text class="tagline" x="600" y="950" text-anchor="middle" font-size="66"
          textLength="940" lengthAdjust="spacingAndGlyphs">World Renowned for Over 45 years</text>
  </svg>
</main>
</body>
</html>
```